Business Card Re-Design...or logo does not look sharp

Hello

We are a start-up and just need someone to help us.

Our colors are: Rosalind charm pink (yeah I know) and charcoal for the lettering.

I am attaching our logo which needs cleaning up.

We want the JUST the lady ironing on the table (pink) in front, and the background in charcoal. All the business info can be on the back.

Dims on card are 2 x 2''

Also, if you have better ideas....please let us know!

Thanks

Gregory

Industry/Entity Type

Business

Contact Information for Business Card

Su Vecina Lavanda
4827 Bellcrest Ln Suite K2
El Paso TX 79912
915-555-0147

```html
<!DOCTYPE html>
<html lang="en">
<head>
<meta charset="utf-8">
<title>Su Vecina Lavanda – Business Card</title>
<link href="https://fonts.googleapis.com/css2?family=Dancing+Script:wght@500;700&family=Courier+Prime&display=swap" rel="stylesheet">
<style>
  :root {
    --charcoal: #4a4a4c;
    --pink: #ee3a6f;
    --paper: #ffffff;
    --backdrop: #d9d9d9;
    --text-grey: #6b6b6b;
    --illustration-grey: #8a8a8a;
  }
  * { box-sizing: border-box; margin: 0; padding: 0; }
  html, body {
    width: 1200px;
    height: 910px;
    overflow: hidden;
    background: var(--backdrop);
  }
  .canvas {
    position: relative;
    width: 1200px;
    height: 910px;
  }
  .card {
    position: absolute;
    left: 250px;
    width: 700px;
    height: 400px;
    background: var(--paper);
    overflow: hidden;
    box-shadow: 0 4px 14px rgba(0,0,0,0.15);
  }
  .card--front { top: 35px; }
  .card--back { top: 475px; }
  .card__wave {
    position: absolute;
    inset: 0;
    width: 100%;
    height: 100%;
  }
  .dot-field { fill: var(--charcoal); }
  .wave-band { fill: var(--pink); }
  .illustration {
    position: absolute;
    border-radius: 6px;
  }
  .card--front .illustration {
    left: 70px;
    top: 205px;
    width: 200px;
    height: 165px;
    background: var(--pink);
  }
  .card--back .illustration {
    left: 85px;
    top: 205px;
    width: 150px;
    height: 120px;
    background: var(--illustration-grey);
  }
  .brand-name {
    position: absolute;
    font-family: "Dancing Script", cursive;
    white-space: nowrap;
  }
  .card--front .brand-name {
    left: 330px;
    top: 270px;
    font-size: 50px;
    font-weight: 500;
    color: var(--charcoal);
  }
  .contact {
    position: absolute;
    left: 275px;
    top: 190px;
  }
  .card--back .brand-name {
    position: static;
    font-size: 40px;
    font-weight: 700;
    color: var(--pink);
    line-height: 1.1;
    margin-bottom: 8px;
  }
  .contact__line {
    font-family: "Courier Prime", monospace;
    font-size: 22px;
    color: var(--text-grey);
    line-height: 1.3;
  }
</style>
</head>
<body>
<main class="canvas">

  <section class="card card--front" aria-label="Card front">
    <svg class="card__wave" viewBox="0 0 700 400" preserveAspectRatio="none">
      <path class="dot-field" role="img" aria-label="Charcoal polka-dot pattern"
            d="M0,0 H700 V145 C620,128 520,110 430,118 C370,124 360,102 300,92 C200,76 90,92 0,140 Z"/>
      <path class="wave-band"
            d="M0,150 C90,102 200,86 300,102 C360,112 370,134 430,128 C520,120 620,138 700,155
               V182 C620,165 520,148 430,156 C365,162 355,140 300,130 C200,114 90,130 0,178 Z"/>
    </svg>
    <div class="illustration" role="img" aria-label="Pink silhouette of a woman ironing at a table"></div>
    <p class="brand-name">Su Vecina Lavanda</p>
  </section>

  <section class="card card--back" aria-label="Card back">
    <svg class="card__wave" viewBox="0 0 700 400" preserveAspectRatio="none">
      <path class="dot-field" role="img" aria-label="Charcoal polka-dot pattern"
            d="M0,0 H700 V110 C620,100 520,92 430,98 C370,102 360,84 300,76 C200,62 90,76 0,112 Z"/>
      <path class="wave-band"
            d="M0,120 C90,86 200,72 300,86 C360,94 370,112 430,108 C520,102 620,110 700,120
               V140 C620,130 520,122 430,128 C365,132 355,114 300,106 C200,92 90,106 0,140 Z"/>
    </svg>
    <div class="illustration" role="img" aria-label="Grey silhouette of a woman ironing at a table"></div>
    <div class="contact">
      <p class="brand-name">Su Vecina Lavanda</p>
      <p class="contact__line">4827 Bellcrest Ln Suite K2</p>
      <p class="contact__line">El Paso TX 79912</p>
      <p class="contact__line">915-555-0147</p>
    </div>
  </section>

</main>
</body>
</html>
```